4th Generation Family Business Needs a New Card Design!

We are a family owned 4th Generation company. We are based in the Sydney, Australia area and we are desperately in need of a more modern and classy card. We are monumental masons who design, supply & erect lasting memorials throughout cemeteries in Sydney. Our customers are normally in a period of grieving. I have attached logo files that will need to be implemented on the card. Company was established 1935. Australian Owned and Operated. Card needs to be designed to PIXO.com specification.

Target Market(s)

Our target market is based upon people that a grieving for family members that have passed away. We also deal with alot of companies that own and operate cemeteries.

Industry/Entity Type

Business

Contact Information for Business Card

Simon Harcourt, Operations Manager, 0417293086, simon@harcourtmemorials.com.au
Lewis Harlund, Director, 0491630572, lewis@harcourtmemorials.com.au
Phone # 02 9561 3048
Website: www.harcourtmemorials.com.au
Address: Suite 17, 8 Palfrey Lane, West Carlow, Sydney NSW 2156

Font styles to use
Serif
Decorative
Script

Requirements
Must have
• Would like to see the logo nicely implemented with a modern design. Embossed lettering would be a nice additive.

```html
<!DOCTYPE html>
<html lang="en">
<head>
<meta charset="utf-8">
<title>Harcourt Memorials – Business Card</title>
<link href="https://fonts.googleapis.com/css2?family=Lato:wght@400;700&display=swap" rel="stylesheet">
<style>
  :root {
    --page: #e4e2df;
    --card-dark: #231f20;
    --card-back: #262526;
    --paper: #ffffff;
    --gold: #e8b92f;
    --ink: #231f20;
    --light: #f2f2f2;
  }
  * { margin: 0; padding: 0; box-sizing: border-box; }
  html, body { width: 1200px; height: 960px; overflow: hidden; background: var(--page); }
  body { position: relative; font-family: 'Lato', sans-serif; }

  .card {
    position: absolute; left: 248px; width: 704px; height: 400px;
    overflow: hidden; box-shadow: 0 4px 14px rgba(0,0,0,.25);
  }
  .card--front { top: 52px; background: var(--card-dark); }
  .card--back { top: 506px; background: var(--card-back); }

  .front-panel { position: absolute; inset: 0; }

  .contact { position: absolute; left: 56px; top: 102px; color: var(--light); }
  .contact__name { color: var(--gold); font-weight: 700; font-size: 24px; letter-spacing: .6px; line-height: 1; }
  .contact__role { font-size: 18px; margin-top: 5px; letter-spacing: .5px; line-height: 1.1; }
  .contact__list { list-style: none; margin-top: 10px; }
  .contact__list li { display: flex; align-items: center; gap: 10px; font-size: 16px; height: 23px; }
  .contact__list svg { width: 14px; height: 14px; flex: none; }

  .company { position: absolute; left: 54px; top: 225px; color: var(--light); font-size: 16px; line-height: 22px; }
  .company__name { color: var(--gold); font-weight: 700; font-size: 17px; }
  .company__list { list-style: none; margin-top: 6px; }
  .company__list li { display: flex; align-items: center; gap: 10px; height: 23px; }
  .company__list svg { width: 14px; height: 14px; flex: none; }

  .wordmark {
    position: absolute; text-align: center; font-family: 'Lato', sans-serif;
    font-weight: 400; text-transform: uppercase; line-height: 1.05;
  }
  .wordmark--front { left: 400px; width: 270px; top: 150px; color: var(--ink); font-size: 40px; letter-spacing: 2px; }
  .wordmark--back { left: 0; width: 704px; top: 140px; color: var(--light); font-size: 52px; letter-spacing: 3px; }
  .wordmark__sub { display: block; font-size: .55em; letter-spacing: 4px; margin-top: 6px; }

  .back-url {
    position: absolute; left: 0; width: 704px; top: 327px; text-align: center;
    color: var(--light); font-size: 16px; letter-spacing: 3.4px;
  }
  .back-url__accent { color: var(--gold); }
</style>
</head>
<body>

<section class="card card--front" aria-label="Business card front">
  <svg class="front-panel" viewBox="0 0 704 400" width="704" height="400" aria-hidden="true">
    <path fill="var(--paper)" d="M205 0 Q255 10 293 33 L293 70 L320 70 Q325 125 360 142 L360 378 L380 378 L399 400 L704 400 L704 0 Z"/>
  </svg>

  <div class="contact">
    <p class="contact__name">Lewis Harlund</p>
    <p class="contact__role">Director</p>
    <ul class="contact__list">
      <li>
        <svg viewBox="0 0 14 14"><rect x="3" y="1" width="8" height="12" rx="1.5" fill="none" stroke="var(--gold)" stroke-width="1.5"/><circle cx="7" cy="10.8" r=".8" fill="var(--gold)"/></svg>
        0491630572
      </li>
      <li>
        <svg viewBox="0 0 14 14"><rect x="1" y="3" width="12" height="8" fill="none" stroke="var(--gold)" stroke-width="1.4"/><path d="M1 3 L7 8 L13 3" fill="none" stroke="var(--gold)" stroke-width="1.4"/></svg>
        lewis@harcourtmemorials.com.au
      </li>
    </ul>
  </div>

  <div class="company">
    <p class="company__name">Harcourt Memorials</p>
    <p>Suite 17, 8 Palfrey Lane</p>
    <p>West Carlow, Sydney NSW 2156</p>
    <ul class="company__list">
      <li>
        <svg viewBox="0 0 14 14"><path d="M9 1 L11.5 2.5 L10 5 Q8 4.8 7 7 Q6 9.5 7.5 11 L6 13.5 Q2 11 4 5.5 Q6 1.5 9 1 Z" fill="var(--gold)"/></svg>
        02 9561 3048
      </li>
      <li>
        <svg viewBox="0 0 14 14" fill="none" stroke="var(--gold)" stroke-width="1.1"><circle cx="7" cy="7" r="6"/><ellipse cx="7" cy="7" rx="2.6" ry="6"/><path d="M1 7 H13 M2 4 H12 M2 10 H12"/></svg>
        www.harcourtmemorials.com.au
      </li>
    </ul>
  </div>

  <p class="wordmark wordmark--front">Harcourt<span class="wordmark__sub">Memorials</span></p>
</section>

<section class="card card--back" aria-label="Business card back">
  <p class="wordmark wordmark--back">Harcourt<span class="wordmark__sub">Memorials</span></p>
  <p class="back-url">www.<span class="back-url__accent">harcourtmemorials</span>.com.au</p>
</section>

</body>
</html>
```